Meridian Tidewren Pale Ale Beer Label/Badge

We need a Beer Label designed for our first official beer to be launched under The meridian Brand!!
It will be a Pale Ale Called "Tidewren Pale Ale"!

The Meridian has the largest Craft Beer & Cider selection in the Geelong & Surf Coast region. With a funky location and a relaxed vibe, Meridian prides itself on serving delicious, unique seasonal food paired with Australia's best Craft Beer. The meridian is the perfect setting for a relaxed afternoon or evening with friends and can package an experience for larger groups or corporate bookings.

The Meridian Tavern brand has been growing for over a year and a half and the first label needs to integrate The meridian Logo but at the same time bring a fresh, new and eye catching feel to it along with embracing the "Odysseus" story in which we will be naming future beers.

The story of Tidewren is found via the following link
http://lorevault.example/wiki/Tidewren_(folklore)

We expect designers to research The meridian Tavern brand along with the all important Craft Beer Market and demographics. This will, potentially, be the start of many more labels to come for the winning designer!!

Requirements
Must have
• The original "O" needs to be integrated into the new logo and as much as the Greek mythology is being used it needs to be certain that this is an original Australian Craft Beer in the modern age!!
strong, modern & unique!!
Nice to have
• Logo could have a depiction of Tidewren
Should not have
• tackiness or cheap!!

```html
<!DOCTYPE html>
<html lang="en">
<head>
<meta charset="utf-8">
<title>Meridian Tidewren Pale Ale – Label Colourways</title>
<link rel="stylesheet" href="https://fonts.googleapis.com/css2?family=Marcellus&family=Roboto+Condensed:wght@700&display=swap">
<style>
  :root {
    --page: #ffffff;
    --panel: #f7f6f4;
    --eyes-a: #e2e0dc;
    --eyes-b: #c9c7c2;
  }
  * { margin: 0; padding: 0; box-sizing: border-box; }
  html, body { width: 1168px; height: 1200px; overflow: hidden; background: var(--page); }
  .canvas { position: relative; width: 1168px; height: 1200px; }

  .label { position: absolute; width: 462px; height: 553px; }
  .label--lime   { left: 125px; top: 35px;
    --frame: #99cc00; --brand: #e8c21e; --mark: #8a8a2a; --title: #b7d52a;
    --style: #e2b81c; --abv: #e2b81c; --place: #7a6a14;
    --scene-a: #d7e88a; --scene-b: #8fbf1e; --scene-c: #8a5a1c; }
  .label--plum   { left: 573px; top: 80px;
    --frame: #880a72; --brand: #880a72; --mark: #8a1a80; --title: #9c1a1a;
    --style: #880a72; --abv: #e2308a; --place: #7a1030;
    --scene-a: #f0c8c8; --scene-b: #d22a2a; --scene-c: #9a2aa0; }
  .label--sea    { left: 297px; top: 600px;
    --frame: #5cf7c6; --brand: #1a3ec8; --mark: #2450d8; --title: #2f74e0;
    --style: #5ce6c0; --abv: #5ce6c0; --place: #1a2a7a;
    --scene-a: #c8daf5; --scene-b: #3a8ae6; --scene-c: #1a2ec0; }

  .label__shape { position: absolute; inset: 0; width: 462px; height: 553px; }
  .label__frame { fill: var(--frame); }
  .label__panel { fill: var(--panel); }

  .label__eyes {
    position: absolute; left: 78px; top: 45px; width: 310px; height: 64px;
    background: linear-gradient(90deg, var(--eyes-a), var(--eyes-b) 25%, var(--eyes-a) 50%, var(--eyes-b) 75%, var(--eyes-a));
    opacity: .75;
  }

  .label__brand {
    position: absolute; left: 78px; width: 310px; top: 48px; text-align: center;
    font-family: "Roboto Condensed", sans-serif; font-weight: 700; font-size: 15px;
    letter-spacing: 1px; color: var(--brand);
  }
  .label__mark {
    position: absolute; left: 210px; top: 72px; width: 46px; height: 46px;
    border-radius: 50%; background: var(--mark);
  }

  .label__title {
    position: absolute; left: 78px; width: 310px; top: 175px; text-align: center;
    font-family: "Marcellus", serif; font-size: 46px; letter-spacing: 1px;
    color: var(--title); line-height: 1;
  }
  .label__style {
    position: absolute; right: 118px; top: 226px; text-align: right;
    font-family: "Roboto Condensed", sans-serif; font-weight: 700; font-size: 14px;
    color: var(--style); white-space: nowrap;
  }
  .label__style .abv { color: var(--abv); }
  .label__place {
    position: absolute; right: 118px; top: 244px; text-align: right;
    font-family: "Roboto Condensed", sans-serif; font-weight: 700; font-size: 9px;
    color: var(--place); white-space: nowrap;
  }
  .label__scene .scene-fill { fill: url(#none); }
</style>
</head>
<body>
<main class="canvas">

  <!-- shared gradient defs -->
  <svg width="0" height="0" style="position:absolute">
    <defs>
      <linearGradient id="scene-lime" x1="0" y1="0" x2="1" y2="1">
        <stop offset="0" stop-color="#d7e88a"/><stop offset=".5" stop-color="#8fbf1e"/><stop offset="1" stop-color="#8a5a1c"/>
      </linearGradient>
      <linearGradient id="scene-plum" x1="0" y1="0" x2="1" y2="1">
        <stop offset="0" stop-color="#f0c8c8"/><stop offset=".5" stop-color="#d22a2a"/><stop offset="1" stop-color="#9a2aa0"/>
      </linearGradient>
      <linearGradient id="scene-sea" x1="0" y1="0" x2="1" y2="1">
        <stop offset="0" stop-color="#c8daf5"/><stop offset=".5" stop-color="#3a8ae6"/><stop offset="1" stop-color="#1a2ec0"/>
      </linearGradient>
    </defs>
  </svg>

  <section class="label label--lime">
    <svg class="label__shape" viewBox="0 0 462 553">
      <polygon class="label__frame" points="75,0 387,0 425,75 425,240 462,280 425,292 425,470 340,553 120,553 38,470 38,292 0,280 38,240 38,75"/>
      <polygon class="label__panel" points="88,37 374,37 390,68 390,488 326,517 134,517 76,488 76,68"/>
      <polygon role="img" aria-label="Tropical island jungle scene in lime and brown tones" fill="url(#scene-lime)" points="76,300 160,284 300,292 390,280 390,488 326,517 134,517 76,488"/>
    </svg>
    <div class="label__eyes" role="img" aria-label="Faint portrait band across the top of the label"></div>
    <div class="label__brand">MERIDIAN</div>
    <div class="label__mark"></div>
    <h1 class="label__title">TIDEWREN</h1>
    <p class="label__style">PALE ALE • <span class="abv">ABV %5</span></p>
    <p class="label__place">Saltmarsh Hill, Victoria, Australia</p>
  </section>

  <section class="label label--plum">
    <svg class="label__shape" viewBox="0 0 462 553">
      <polygon class="label__frame" points="75,0 387,0 425,75 425,240 462,280 425,292 425,470 340,553 120,553 38,470 38,292 0,280 38,240 38,75"/>
      <polygon class="label__panel" points="88,37 374,37 390,68 390,488 326,517 134,517 76,488 76,68"/>
      <polygon role="img" aria-label="Tropical island jungle scene in red and violet tones" fill="url(#scene-plum)" points="76,300 160,284 300,292 390,280 390,488 326,517 134,517 76,488"/>
    </svg>
    <div class="label__eyes" role="img" aria-label="Faint portrait band across the top of the label"></div>
    <div class="label__brand">MERIDIAN</div>
    <div class="label__mark"></div>
    <h1 class="label__title">TIDEWREN</h1>
    <p class="label__style">PALE ALE • <span class="abv">ABV %5</span></p>
    <p class="label__place">Saltmarsh Hill, Victoria, Australia</p>
  </section>

  <section class="label label--sea">
    <svg class="label__shape" viewBox="0 0 462 553">
      <polygon class="label__frame" points="75,0 387,0 425,75 425,240 462,280 425,292 425,470 340,553 120,553 38,470 38,292 0,280 38,240 38,75"/>
      <polygon class="label__panel" points="88,37 374,37 390,68 390,488 326,517 134,517 76,488 76,68"/>
      <polygon role="img" aria-label="Tropical island jungle scene in blue tones" fill="url(#scene-sea)" points="76,300 160,284 300,292 390,280 390,488 326,517 134,517 76,488"/>
    </svg>
    <div class="label__eyes" role="img" aria-label="Faint portrait band across the top of the label"></div>
    <div class="label__brand">MERIDIAN</div>
    <div class="label__mark"></div>
    <h1 class="label__title">TIDEWREN</h1>
    <p class="label__style">PALE ALE • <span class="abv">ABV %5</span></p>
    <p class="label__place">Saltmarsh Hill, Victoria, Australia</p>
  </section>

</main>
</body>
</html>
```